Harborline Benches business cards

I’d like a business card design that includes my logo, a tag line and my contact info. Black, textured background. My contact info color should match the orange and blue gradients. Tagline under logo: “Wooden Tables and Furniture of the Highest Quality”

Target Market(s)

High end furniture buyers

Contact Information for Business Card

Contact info, logo and tagline

```html
<!DOCTYPE html>
<html lang="en">
<head>
<meta charset="UTF-8">
<title>Harborline Benches – Business Cards</title>
<link href="https://fonts.googleapis.com/css2?family=Bebas+Neue&family=Poppins:wght@400;500&family=Ubuntu:wght@500&display=swap" rel="stylesheet">
<style>
  :root {
    --orange: #ec7226;
    --blue: #1f5aa8;
    --ink: #1c1c1c;
    --rule: #9a9a9a;
    --paper: #ffffff;
    --backdrop: #d9d9d9;
  }
  * { margin: 0; padding: 0; box-sizing: border-box; }
  html, body { width: 1200px; height: 1200px; overflow: hidden; }
  body {
    background: var(--backdrop);
    display: flex;
    align-items: center;
    justify-content: center;
    gap: 30px;
  }
  .card {
    position: relative;
    width: 368px;
    height: 594px;
    overflow: hidden;
  }
  /* Front */
  .card-front { background: var(--orange); }
  .front-art {
    position: absolute; inset: 0;
    background:
      radial-gradient(ellipse 90% 70% at 100% 0%, rgba(31,90,168,1) 0%, rgba(31,90,168,0.55) 40%, rgba(31,90,168,0) 75%),
      linear-gradient(180deg, #7e6a6a 0%, #a66a4c 35%, var(--orange) 65%, var(--orange) 100%);
  }
  .tagline {
    position: absolute; left: 48px; right: 40px; top: 136px;
    font-family: "Bebas Neue", sans-serif;
    color: var(--paper);
    line-height: 1;
  }
  .tagline .line { display: block; font-size: 57px; height: 68px; letter-spacing: -0.5px; }
  .tagline .emphasis { display: block; font-size: 101px; letter-spacing: 4px; margin-top: 20px; margin-left: -3px; }
  /* Back */
  .card-back { background: var(--paper); }
  .brand {
    position: absolute; top: 132px; left: 0; right: 0;
    display: flex; align-items: center; justify-content: center; gap: 8px;
    font-family: "Poppins", sans-serif; font-weight: 500;
    font-size: 27px; color: var(--orange);
  }
  .brand-dot { width: 12px; height: 12px; border-radius: 50%; background: var(--orange); }
  .person { position: absolute; top: 330px; left: 0; right: 0; text-align: center; }
  .person-name { font-family: "Ubuntu", sans-serif; font-weight: 500; font-size: 29px; line-height: 1.1; }
  .person-name .first { color: var(--orange); }
  .person-name .last { color: var(--blue); }
  .person-role { font-family: "Poppins", sans-serif; font-size: 16px; color: var(--ink); margin-top: 2px; }
  .icon-row {
    position: absolute; top: 396px; left: 87px; right: 87px;
    display: flex; align-items: center; gap: 4px;
  }
  .icon-row .rule { flex: 1; height: 1px; background: var(--rule); }
  .icon-row .icons { display: flex; gap: 4px; margin: 0 4px; }
  .icon { width: 25px; height: 25px; border-radius: 3px; background: var(--orange); display: flex; align-items: center; justify-content: center; }
  .contact, .address {
    position: absolute; left: 0; right: 0; text-align: center;
    font-family: "Poppins", sans-serif; font-size: 17px; color: var(--ink); line-height: 21px;
  }
  .contact { top: 427px; }
  .divider { position: absolute; top: 507px; left: 88px; right: 80px; height: 1px; background: var(--rule); }
  .address { top: 520px; }
</style>
</head>
<body>
  <section class="card card-front">
    <div class="front-art" role="img" aria-label="Faint bare tree silhouette over an orange to blue gradient"></div>
    <h1 class="tagline">
      <span class="line">Wooden Tables</span>
      <span class="line">and Furniture</span>
      <span class="line">of the Highest</span>
      <span class="emphasis">Quality</span>
    </h1>
  </section>

  <section class="card card-back">
    <div class="brand"><span class="brand-dot"></span><span class="brand-name">Harborline Benches</span></div>

    <div class="person">
      <div class="person-name"><span class="first">Daniel</span> <span class="last">Whitford</span></div>
      <div class="person-role">Managing Director</div>
    </div>

    <div class="icon-row">
      <span class="rule"></span>
      <div class="icons">
        <span class="icon" aria-label="Phone">
          <svg width="16" height="14" viewBox="0 0 16 14"><path d="M1 5 Q8 0 15 5 L13 7 L11 5.5 L5 5.5 L3 7 Z" fill="#fff"/><rect x="4" y="7" width="8" height="6" rx="1" fill="#fff"/></svg>
        </span>
        <span class="icon" aria-label="Email">
          <svg width="16" height="12" viewBox="0 0 16 12"><rect x="1" y="1" width="14" height="10" fill="none" stroke="#fff" stroke-width="1.4"/><path d="M1 1 L8 7 L15 1 M1 11 L6 5.5 M15 11 L10 5.5" fill="none" stroke="#fff" stroke-width="1.2"/></svg>
        </span>
        <span class="icon" aria-label="Website">
          <svg width="16" height="16" viewBox="0 0 16 16"><circle cx="8" cy="8" r="7" fill="#fff"/><path d="M4 5 Q6 3 8 5 Q7 8 5 8 Z M9 9 Q12 8 12 11 Q10 13 9 11 Z" fill="var(--orange)"/></svg>
        </span>
      </div>
      <span class="rule"></span>
    </div>

    <div class="contact">
      <div>055-210 348 617</div>
      <div>hello@harborline.com</div>
      <div>www.harborline.com</div>
    </div>

    <div class="divider"></div>

    <div class="address">
      <div>421, Address line goes here</div>
      <div>45452,Country Name</div>
    </div>
  </section>
</body>
</html>
```